tallow-brook.com

We are a small dollar lending company that will revolutionize the industry. We will do this by being completely transparent, fee free, etc and an interest rate that normal people can afford to pay. Over 10X less than our competition. We only allow our members to pay bills " bills paid fast", within 72 hours. Payday loans typically charge from 390%-600% with a terrible payback structure. We charge 36%, period, with a payback structure over 12 months. Our site will be very simple and easy to use but elegant at the same time. We do not want the site to be too busy, less is more and easier. We will have; Home, The Story, Why tallowbrook.com, Are you eligible? Members, Clients. To become a member you have to be referred by a current client of tallowbrook.com. A lot of the busy stuff will be saved for the Members and Clients sections. The feel must be elegant, easy to use and very simple to understand. I am looking for the green, white and black combinations of colors, very similar to my logo that was designed by Fernquillo.

```html
<!DOCTYPE html>
<html lang="en">
<head>
<meta charset="utf-8">
<title>Tallow Brook — Home</title>
<link href="https://fonts.googleapis.com/css2?family=Source+Sans+3:ital,wght@0,400;0,600;1,400&display=swap" rel="stylesheet">
<style>
  :root{
    --green:#5cb531;
    --green-light:#8dc63f;
    --green-dark:#5fb22e;
    --ink:#3a3a3a;
    --text:#6b6b6b;
    --page:#f8f8f8;
    --footer:#2c2c2c;
    --white:#ffffff;
  }
  *{margin:0;padding:0;box-sizing:border-box}
  html,body{width:1200px;height:1162px;overflow:hidden}
  body{background:var(--page);font-family:"Source Sans 3",sans-serif;color:var(--text);position:relative}
  a{color:inherit;text-decoration:none}

  .brand{position:absolute;left:132px;top:37px;display:flex;align-items:center;gap:10px}
  .brand-mark{width:55px;height:55px;background:var(--green);border-radius:6px}
  .brand-name{font-size:26px;font-weight:400;color:var(--ink);letter-spacing:-.3px}

  .login{position:absolute;left:991px;top:27px;width:78px;height:34px;background:var(--green-light);border:1px solid #6aa82a;color:var(--white);font-size:14px;display:flex;align-items:center;justify-content:center}

  .main-nav{position:absolute;right:133px;top:85px;display:flex;gap:31px;font-size:14px;color:var(--ink);text-transform:uppercase}
  .main-nav .active{color:var(--green)}

  .hero{position:absolute;left:130px;top:126px;width:940px;height:389px;border-radius:3px;overflow:hidden;
    background:radial-gradient(ellipse at 55% 60%,#eef2f5 0%,#c9d6df 55%,#a9bccb 100%)}
  .hero-art{position:absolute;inset:0}
  .hero-note{position:absolute;left:615px;top:151px;width:321px;height:118px;background:rgba(255,255,255,.72);text-align:right;padding:8px 20px 0 0;color:#555;font-size:13.5px;line-height:1.2}
  .hero-note .big{color:var(--green);font-size:34px}
  .hero-note .mid{color:var(--green);font-size:24px}
  .dots{position:absolute;left:437px;top:358px;display:flex;gap:3px}
  .dots span{width:16px;height:16px;border-radius:50%;background:#b8b8b8}
  .dots span.on{background:var(--green)}

  .welcome{position:absolute;left:132px;top:576px;width:612px}
  .welcome h1{font-weight:400;font-size:26px;color:var(--ink)}
  .welcome h1 em{font-style:normal;color:var(--green)}
  .welcome p{margin-top:17px;font-size:13.6px;line-height:23px}
  .welcome .more{color:var(--green);font-style:italic;margin-left:6px}
  .team-photo{position:absolute;left:770px;top:582px;width:300px;height:187px;background:linear-gradient(120deg,#e8e9ec 0%,#d9d4cf 50%,#f1f1f1 100%)}

  .features{position:absolute;top:828px;left:128px;width:944px;height:181px}
  .feature{position:absolute;top:0;width:303px;height:181px;border:1px solid #59a82a;background:linear-gradient(#8cc83c,#65b530);color:var(--white)}
  .feature svg{position:absolute;left:18px;top:18px}
  .feature h2{position:absolute;top:20px;font-weight:600;font-size:22px;text-transform:uppercase;letter-spacing:-.2px}
  .feature h3{position:absolute;top:54px;font-weight:400;font-size:14px}
  .feature p{position:absolute;left:18px;right:14px;top:96px;font-size:13.6px;line-height:19px}

  .site-footer{position:absolute;left:0;top:1058px;width:1200px;height:104px;background:var(--footer);color:#e8e8e8}
  .footer-nav{position:absolute;left:133px;top:28px;font-size:13px;display:flex}
  .footer-nav a+a::before{content:"|";margin:0 12px}
  .copyright{position:absolute;left:133px;top:61px;font-size:11.5px}
  .copyright span{color:var(--green-light)}
  .social{position:absolute;left:939px;top:40px;display:flex;gap:5px}
  .social span{width:28px;height:28px;border-radius:50%;background:#e9e9e9}
</style>
</head>
<body>

<header>
  <a class="brand" href="#"><span class="brand-mark"></span><span class="brand-name">Tallow Brook</span></a>
  <a class="login" href="#">LOGIN</a>
  <nav class="main-nav">
    <a class="active" href="#">Home</a>
    <a href="#">The Story</a>
    <a href="#">Why tallowbrook.com</a>
    <a href="#">Are you eligible?</a>
    <a href="#">Members</a>
    <a href="#">Clients</a>
  </nav>
</header>

<section class="hero">
  <div class="hero-art" role="img" aria-label="Photo: a hand pouring from a metal watering can onto a leafy plant shaped like a dollar sign, pale blue backdrop"></div>
  <div class="hero-note">
    We charge only <span class="big">36%</span> &amp;<br>
    give <span class="mid">over 12 months time</span><br>
    to pay back, no fees, hidden costs etc.
  </div>
  <div class="dots"><span class="on"></span><span></span><span></span><span></span></div>
</section>

<section class="welcome">
  <h1>Welcome to Our Website <em>Mainpage..</em></h1>
  <p>Lorem ipsum dolor sit amet, consectetur adipisicing elit, sed do eiusmod tempor incididunt ut labore et dolore magna aliqua. Ut enim ad minim veniam, quis nostrud exercitation ullamco laboris nisi ut aliquip ex ea commodo consequat. Lorem ipsum dolor sit amet, consectetur adipisicing elit, sed do eiusmodus tempor incididunt ut labore et dolore magna aliqua. Ut enim ad minim veniam, quis nostrud exercitaton ullamco laboris nisi ut aliquip ex ea commodo consequat. Lorem ipsum dolor sit amet, consectetur adipi-sicing elit, sed do eiusmod tempor incididunt ut labore et dolore. <a class="more" href="#">Read More &gt;&gt;</a></p>
</section>
<div class="team-photo" role="img" aria-label="Photo: a smiling group of business professionals standing in a row"></div>

<section class="features">
  <article class="feature" style="left:0">
    <svg width="44" height="56" viewBox="0 0 44 56" fill="#2b2b2b"><rect x="0" y="0" width="44" height="56" rx="6"/><rect x="6" y="6" width="32" height="15" rx="2" fill="#7abf36"/><g fill="#7abf36"><rect x="7" y="27" width="8" height="8" rx="1"/><rect x="18" y="27" width="8" height="8" rx="1"/><rect x="29" y="27" width="8" height="8" rx="1"/><rect x="7" y="39" width="8" height="8" rx="1"/><rect x="18" y="39" width="8" height="8" rx="1"/><rect x="29" y="39" width="8" height="8" rx="1"/></g></svg>
    <h2 style="left:83px">Calculate</h2>
    <h3 style="left:83px">How Much Do I have to payback</h3>
    <p>Lorem ipsum dolor sit amet, consectetur adip isicing elit, sed do eiusmod tempor incididunt ut labore et dolore magna aliqua.</p>
  </article>
  <article class="feature" style="left:320px">
    <svg width="56" height="50" viewBox="0 0 56 50"><path d="M28 3 L53 47 H3 Z" fill="none" stroke="#2b2b2b" stroke-width="5" stroke-linejoin="round"/><rect x="25.5" y="17" width="5" height="17" fill="#2b2b2b"/><circle cx="28" cy="40" r="3" fill="#2b2b2b"/></svg>
    <h2 style="left:91px">Are you Eligble</h2>
    <h3 style="left:93px;top:52px">You Must be Referred</h3>
    <p style="left:16px">Lorem ipsum dolor sit amet, consectetur adip isicing elit, sed do eiusmod tempor incididunt ut labore et dolore magna aliqua.</p>
  </article>
  <article class="feature" style="left:641px">
    <svg width="70" height="50" viewBox="0 0 70 50" fill="#2b2b2b"><rect x="22" y="2" width="44" height="8" rx="4"/><rect x="26" y="13" width="42" height="8" rx="4"/><rect x="24" y="24" width="44" height="8" rx="4"/><rect x="26" y="35" width="42" height="8" rx="4"/><circle cx="20" cy="30" r="17" stroke="#7abf36" stroke-width="2"/><text x="20" y="38" font-size="22" font-family="sans-serif" text-anchor="middle" fill="#7abf36">$</text></svg>
    <h2 style="left:107px">Pay Bills</h2>
    <h3 style="left:109px;top:51px">Bills Paid Fast</h3>
    <p style="top:98px">Lorem ipsum dolor sit amet, consectetur adip isicing elit, sed do eiusmod tempor incididunt ut labore et dolore magna aliqua.</p>
  </article>
</section>

<footer class="site-footer">
  <nav class="footer-nav">
    <a href="#">Home</a><a href="#">The Story</a><a href="#">Why tallowbrook.com</a><a href="#">Are you eligible?</a><a href="#">Members</a><a href="#">Clients</a>
  </nav>
  <p class="copyright">© Copyright 2014 <span>tallow-brook.</span> All rights reserved.</p>
  <div class="social" aria-label="Social links"><span></span><span></span><span></span><span></span></div>
</footer>

</body>
</html>
```